Harborview Estates Business Card for Apartment Buildings

Create business cards for resident managers who run apartment buildings. The audience is the public who are searching for apartment rentals, and current residents who live at the apartment building. Key design element will be incorporating the company logo, however, the logo cannot dominate. The building name and manager name are more important than the logo. Current business card design leaves little room for copy, so we may need to reduce the size on the current card to allow for more space for copy.

Target Market(s)

Adults 18-65 years of age, who are looking for an apartment rental, plus current residents who live at our apartment buildings.

Industry/Entity Type

Property Management

Contact Information for Business Card

A major design element will be use of the company logo. Important property and manager contact information must be part of the design. The size of the logo will need to be reduced to make room for building and manager contact copy.

Font styles to use
Sans Serif

Colors
3176b5
000000
959595
ffffff

Requirements
Must have
• 1) Incorporate the company logo.
• 2) Use the company colors (dark blue, black/grey, over white).
• 3) FEATURE THE BUILDING NAME
• 4) FEATURE THE MANAGER NAME
• 5) The company name is less important than BUILDING and MANAGER
• 6) Manager contact information
• **SEE ATTACHED CREATIVE BRIEF**
Nice to have
• 1) Back of card logo watermark
• 2) Ability to write notes on back of carfd
Should not have
• Avoid letting the company logo dominate the card, the building name and manager are more important than the company logo.

```html
<!DOCTYPE html>
<html lang="en">
<head>
<meta charset="UTF-8">
<title>Harborview Estates Business Card</title>
<link rel="stylesheet" href="https://fonts.googleapis.com/css2?family=Roboto:wght@400;700&display=swap">
<style>
  :root {
    --brand-blue: #3176b5;
    --brand-blue-soft: #9fb6e3;
    --ink: #000000;
    --ink-grey: #4a4a4a;
    --muted-grey: #959595;
    --paper: #ffffff;
    --backdrop: #eef0f2;
  }
  * { box-sizing: border-box; margin: 0; padding: 0; }
  html, body {
    width: 1200px; height: 1000px; overflow: hidden;
    background: var(--backdrop);
    font-family: "Roboto", Arial, sans-serif;
  }
  .sheet {
    width: 1200px; height: 1000px;
    display: flex; flex-direction: column; align-items: center; justify-content: center;
    gap: 60px;
  }
  .card {
    position: relative;
    width: 700px; height: 400px;
    background: var(--paper);
    box-shadow: 0 6px 18px rgba(0,0,0,0.12);
    overflow: hidden;
  }
  /* Front */
  .card-front .brand {
    position: absolute; left: 40px; top: 60px;
    display: flex; align-items: center; gap: 10px;
  }
  .brand-mark { width: 30px; height: 30px; background: var(--brand-blue); flex: none; }
  .brand-name {
    color: var(--brand-blue); font-weight: 700; font-size: 21px;
    line-height: 1.05; letter-spacing: 0.3px; text-transform: uppercase;
  }
  .divider {
    position: absolute; left: 272px; top: 0; width: 3px; height: 340px;
    background: var(--brand-blue);
  }
  .manager {
    position: absolute; left: 40px; top: 214px; width: 225px;
  }
  .manager-name {
    color: var(--brand-blue); font-weight: 700; font-size: 22px; text-transform: uppercase;
    white-space: nowrap;
  }
  .manager-role { color: var(--ink-grey); font-size: 14px; margin-top: 2px; }
  .contact {
    position: absolute; left: 300px; top: 112px;
    color: var(--ink-grey); font-size: 16px; line-height: 1.35;
  }
  .contact-address { margin-bottom: 16px; }
  .contact-list { list-style: none; }
  .contact-list li { display: flex; line-height: 1.75; white-space: nowrap; }
  .contact-label { width: 62px; color: var(--ink); font-weight: 700; }
  .band {
    position: absolute; left: 0; bottom: 24px; width: 100%; height: 22px;
    background: var(--brand-blue);
  }
  /* Back */
  .card-back { display: flex; align-items: center; justify-content: center; gap: 18px; }
  .card-back .brand-mark { width: 64px; height: 84px; background: var(--brand-blue-soft); }
  .card-back .brand-name {
    color: var(--brand-blue-soft); font-size: 48px; line-height: 1.1; letter-spacing: 3px;
  }
</style>
</head>
<body>
<main class="sheet">
  <section class="card card-front" aria-label="Business card front">
    <div class="brand">
      <span class="brand-mark"></span>
      <span class="brand-name">Harborview<br>Estates LLC</span>
    </div>
    <div class="divider"></div>
    <div class="manager">
      <p class="manager-name">Daniel Hayes</p>
      <p class="manager-role">Property Manager</p>
    </div>
    <div class="contact">
      <p class="contact-address">2750 Cedar Ridge Road #B210<br>Fairview, CA 90412</p>
      <ul class="contact-list">
        <li><span class="contact-label">Phone</span>:- 555-310-4827</li>
        <li><span class="contact-label">Fax</span>:- 555-310-4830</li>
        <li><span class="contact-label">Email</span>:- daniel@harborviewestates.us</li>
        <li><span class="contact-label">Web</span>:- www.harborviewestates.us</li>
      </ul>
    </div>
    <div class="band"></div>
  </section>

  <section class="card card-back" aria-label="Business card back">
    <span class="brand-mark"></span>
    <span class="brand-name">Harborview<br>Estates LLC</span>
  </section>
</main>
</body>
</html>
```